Zielgruppe
Beamer Vermietung
Aufgabenstellung
Erstellung 2 professionell aussehender Webseiten.
Projektor-Verleih-Raum-Ostlingen.de
sowie
Projektor-Verleih-Raum-Wendbergshof.de
Die Seiten sind aktuell im Betrieb, aber haben ein sehr veraltetes Design.
Die Seiten können ähnlich aussehen, sollten aber etwas unterschiedlich sein, damit sie für den Kunden leicht anders aussehen.
Wichtig ist, dass alle Seiten, inklusive Startseite, Unterseiten und Links designed werden und das dieses Design in die bestehende PressKern Installation eingepflegt wird.
Es ist also notwendig, gute PressKern Kenntnisse zu haben um dann auch zwei fertige PressKern Seiten liefern zu können.

```html
<!DOCTYPE html>
<html lang="de">
<head>
<meta charset="utf-8">
<title>Projektor-Verleih Raum Ostlingen</title>
<link href="https://fonts.googleapis.com/css2?family=Roboto:wght@300;400;500;700;900&family=Roboto+Condensed:wght@400&display=swap" rel="stylesheet">
<style>
:root{
  --navy:#1f3c68;
  --navy-dark:#1a3258;
  --yellow:#f5c51c;
  --band:#eeeef0;
  --topbar:#efefef;
  --text-grey:#555;
  --muted:#9a9a9a;
  --white:#fff;
}
*{margin:0;padding:0;box-sizing:border-box}
html,body{width:810px;height:1200px;overflow:hidden}
body{position:relative;background:var(--white);font-family:'Roboto',sans-serif;color:var(--navy)}
.abs{position:absolute}
.topbar{left:0;top:0;width:810px;height:21px;background:var(--topbar);border-bottom:1px solid #ddd}
.topbar .domain{left:110px;top:5px;font-size:7.5px;color:#444}
.social{top:5px;width:11px;height:11px;border-radius:50%;background:var(--navy)}
.social.active{background:var(--yellow)}
.site-header{left:0;top:21px;width:810px;height:47px;background:var(--white)}
.site-title{left:107px;top:31px;font-family:'Roboto Condensed',sans-serif;font-size:18.5px;color:var(--navy)}
.header-links{top:37px;font-size:9px;font-weight:500;color:var(--navy);display:flex;align-items:center;gap:4px}
.mainnav{left:0;top:68px;width:810px;height:33px;background:var(--navy)}
.mainnav a{position:absolute;top:0;height:33px;line-height:33px;font-size:9.5px;font-weight:500;color:var(--white);text-decoration:none;padding:0 6px}
.mainnav a.current{background:var(--yellow);color:var(--navy)}
.hero{left:0;top:101px;width:810px;height:310px;background:linear-gradient(100deg,#b9a77e 0%,#7c86a8 35%,#3c54a0 60%,#a9abcb 85%,#c8b891 100%)}
.hero-accent{left:110px;top:163px;width:18px;height:2px;background:var(--yellow)}
.hero-title{left:109px;top:168px;font-size:32.5px;font-weight:700;line-height:36px;color:var(--white);white-space:nowrap}
.hero-sub{left:110px;top:249px;font-size:14px;font-weight:300;line-height:18.5px;color:var(--white);letter-spacing:.2px}
.btn{left:110px;top:313px;width:96px;height:25px;border-radius:13px;background:var(--yellow);color:var(--navy);font-size:9.5px;font-weight:700;text-align:center;line-height:25px}
.band{left:0;top:411px;width:810px;height:57px;background:var(--band)}
.band-text{left:141px;top:426px;font-size:24px;font-weight:700;color:var(--navy);white-space:nowrap;z-index:1}
.price{position:relative;display:inline-block;padding:0 3px;z-index:0}
.price::before{content:"";position:absolute;left:-2px;top:-11px;width:47px;height:47px;border-radius:50%;background:var(--yellow);z-index:-1}
.price span{text-decoration:underline;text-decoration-thickness:1px}
.intro{left:110px;top:490px}
.intro h2{font-size:21px;font-weight:500}
.intro p{margin-top:8px;font-size:14px;font-weight:300;color:var(--text-grey)}
.product{background:radial-gradient(ellipse at center,#8d8f94 0%,#c9cacd 55%,#fff 78%)}
.tagline{left:107px;top:944px;font-size:18px;font-weight:300;line-height:22px}
.tagline .sub{color:var(--muted)}
.cta{left:0;top:1036px;width:810px;height:114px;background:var(--navy)}
.cta h3{position:absolute;left:0;width:810px;top:20px;text-align:center;font-size:27.5px;font-weight:500;color:var(--yellow)}
.phone{top:65px;font-size:21px;font-weight:300;color:var(--white);display:flex;align-items:center;gap:12px}
.footer{left:0;top:1150px;width:810px;height:50px;background:var(--navy-dark);color:#d7dbe4;font-size:7.5px;text-align:center;line-height:15px;padding-top:9px}
</style>
</head>
<body>
<div class="abs topbar">
  <span class="abs domain">projektor-verleih-raum-ostlingen.de</span>
  <span class="abs social active" style="left:625px"></span>
  <span class="abs social" style="left:645px"></span>
  <span class="abs social" style="left:665px"></span>
  <span class="abs social" style="left:685px"></span>
</div>

<div class="abs site-header"></div>
<div class="abs site-title">Projektor-Verleih zu günstigen Konditionen</div>
<div class="abs header-links" style="left:468px">
  <svg width="11" height="10" viewBox="0 0 11 10"><path d="M5.5 0 0 5h1.5v5h3V7h2v3h3V5H11z" fill="#1f3c68"/></svg>
  <span>&nbsp;Startseite</span>
</div>
<div class="abs header-links" style="left:539px">Impressum</div>
<div class="abs header-links" style="left:603px">
  <svg width="13" height="9" viewBox="0 0 13 9"><rect x=".5" y=".5" width="12" height="8" fill="none" stroke="#1f3c68"/><path d="M.5.5 6.5 5l6-4.5" fill="none" stroke="#1f3c68"/></svg>
  <span>&nbsp;Kontakt / Anreisev</span>
</div>

<nav class="abs mainnav">
  <a class="current" style="left:109px;width:84px;padding-left:6px">Beamer mieten</a>
  <a style="left:197px">HD-Beamer mieten</a>
  <a style="left:301px">Full HD-Beamer</a>
  <a style="left:391px">Leinwand mieten</a>
  <a style="left:488px">Reservierung</a>
  <a style="left:566px">Preisliste</a>
  <a style="left:628px">Datenschutz</a>
</nav>

<div class="abs hero" role="img" aria-label="Foto: Projektor auf einem Ständer in einem Konferenzsaal"></div>
<div class="abs hero-accent"></div>
<h1 class="abs hero-title">Beamer-Vermietung im<br>Raum Ostlingen / Talbrück</h1>
<div class="abs hero-sub">Jetzt neu: HD-Beamer für das perfekte Bilderlebnis<br>zu günstigen Konditionen!</div>
<div class="abs btn">KONTAKT</div>

<div class="abs band"></div>
<svg class="abs" style="left:76px;top:426px" width="34" height="30" viewBox="0 0 34 30"><circle cx="10" cy="19" r="8" fill="#f5c51c"/><circle cx="28" cy="6" r="3.5" fill="#1f3c68"/></svg>
<div class="abs band-text">Projektoren und Leinwände ab bereits <span class="price"><span>30€</span></span> pro Tag</div>

<div class="abs intro">
  <h2>! Beamer mieten zu TOP-Konditionen !</h2>
  <p>NEU: Jetzt auch HD-Beamer!</p>
</div>

<div class="abs product" style="left:106px;top:585px;width:172px;height:100px" role="img" aria-label="Produktfoto: dunkler Beamer"></div>
<div class="abs product" style="left:311px;top:585px;width:170px;height:100px" role="img" aria-label="Produktfoto: weißer Beamer"></div>
<div class="abs product" style="left:503px;top:580px;width:193px;height:108px" role="img" aria-label="Produktfoto: schwarzer Heimkino-Beamer"></div>
<div class="abs product" style="left:120px;top:723px;width:250px;height:200px" role="img" aria-label="Produktfoto: grauer Beamer mit Fernbedienung"></div>
<div class="abs product" style="left:380px;top:723px;width:270px;height:175px" role="img" aria-label="Produktfoto: silberner Beamer mit Fernbedienung"></div>

<div class="abs tagline">Projektor-Verleih-Raum-Ostlingen.de<br><span class="sub">Ihre Adresse für Beamer Anmietung / Beamer Vermietung!</span></div>

<section class="abs cta">
  <h3>Reservieren oder Buchen</h3>
  <div class="abs phone" style="left:168px">
    <svg width="22" height="16" viewBox="0 0 22 16"><path d="M1 5c0-3 4-4 10-4s10 1 10 4v2h-5V5H6v2H1z" fill="#f5c51c"/><path d="M5 8h12l3 7H2z" fill="#f5c51c"/><circle cx="11" cy="11.5" r="2.3" fill="#1f3c68"/></svg>
    <span>02631/550412</span>
  </div>
  <div class="abs phone" style="left:435px">
    <svg width="24" height="28" viewBox="0 0 24 28"><rect x="1" y="2" width="16" height="25" rx="2" fill="none" stroke="#f5c51c" stroke-width="1.4"/><line x1="1" y1="22" x2="17" y2="22" stroke="#f5c51c"/><path d="M5 10q1 5 6 7l1.5-1.5-2-1.5-1 1q-2-1-3-3l1-1-1.5-2z" fill="none" stroke="#f5c51c"/><path d="M19 3q2 2 0 4M21 1q3.5 4 0 8" fill="none" stroke="#f5c51c"/></svg>
    <span>0151/4427093</span>
  </div>
</section>

<footer class="abs footer">
  Copyright © 2020 Projektor-Verleih-Raum-Wendbergshof.de – Beamer mieten in Wendbergshof. Alle Rechte vorbehalten.<br>
  Theme: Farbblatt von Themenwerk. Bereitgestellt von PressKern.
</footer>
</body>
</html>
```